The Korvane LLC Asset Classes

I'm looking for for two designs here to go into powerpoint and potentially as a standalone PDF. My company does wealth management.
Graphic Image #1
I break down the investment world into 4 broad categories
-Preservation
-Capital Markets
-Real Estate
-Alternatives
In each broad category, there are subcategories:
Preservation: cash, checking/savings accounts, money market accounts, CD's, and fixed annuities.
Capital Markets: Publicly traded stocks and bonds
Real Estate: single-family residence, retail, industrial, multifamily, and office
Alternatives: private equity, private credit, cryptocurrency, asset-backed loans, tax liens, oil & gas, litigation finance, and royalties
Graphic 2: Please see the bottom f page 1 of the Tessolin Decks PDF.
Just like in graphic one, you have 4 categories of the Capital Markets and their respective subcategories
Category 1: Domestic Stocks: Subcategories are Large, mid, and small size companies
Category 2: International Stocks: Subcategories are Large, Mid/Small and by region - Developed and Emerging
Category 3: Fixed Income: You have subcategories like corporate, municipal, government, domestic, international
Category 4: Alternatives: The subcategories are metals and real estate
---------------------
I'm looking to create a graphic (either pie chart, or a circle broken into parts or some other clever way to illustrate this) to clearly illustrate both of these universes in a clean, professional, slick manner.
Target Market(s)
Investors
Colors
Designer to choose colors to be used in the design.
Requirements
Must have
- Clean
- professional
- Easy to read
- Creative
- Visually appealling
Nice to have
- I have attached my logo and some marketing materials so you can get a feel of what I am doing. Maybe you can clean this up too!

```html
<!DOCTYPE html>
<html lang="en">
<head>
<meta charset="utf-8">
<title>Total Asset Allocation</title>
<link rel="stylesheet" href="https://fonts.googleapis.com/css2?family=Jost:wght@600&family=Source+Sans+3:wght@400;500&display=swap">
<style>
  :root {
    --title-orange: #f0914a;
    --brand-blue: #1c5f8a;
    --text-body: #3a3a3a;
    --green: #45af47;
    --green-dark: #177a1c;
    --green-head: #1b6e1f;
    --blue: #0868ae;
    --blue-dark: #034a78;
    --blue-head: #0d3b66;
    --brown: #ae7e52;
    --brown-dark: #5e3a1c;
    --brown-head: #5a3215;
    --gray: #a3a3a3;
    --gray-dark: #6e6e6e;
    --gray-head: #555555;
    --slide-top: #ffffff;
    --slide-bottom: #a8b9cb;
  }
  * { box-sizing: border-box; margin: 0; padding: 0; }
  html, body { width: 1200px; height: 1000px; overflow: hidden; }
  body {
    font-family: "Source Sans 3", "Segoe UI", sans-serif;
    background: var(--slide-top);
  }
  .slide {
    position: relative;
    width: 1200px;
    height: 1000px;
    overflow: hidden;
    background: linear-gradient(to bottom, var(--slide-top) 0%, var(--slide-top) 38%, #dfe5ec 62%, var(--slide-bottom) 100%);
  }
  .slide-title {
    position: absolute;
    left: 48px;
    top: 52px;
    font-size: 46px;
    font-weight: 400;
    color: var(--title-orange);
    letter-spacing: 0.5px;
  }
  .brand {
    position: absolute;
    right: 52px;
    top: 64px;
    display: flex;
    align-items: center;
    gap: 12px;
  }
  .brand-dot {
    width: 30px;
    height: 30px;
    border-radius: 50%;
    background: var(--brand-blue);
  }
  .brand-name {
    font-size: 36px;
    font-weight: 500;
    color: var(--brand-blue);
  }
  .category {
    position: absolute;
    top: 290px;
    width: 250px;
    height: 710px;
  }
  .category:nth-of-type(1) { left: 66px; }
  .category:nth-of-type(2) { left: 340px; }
  .category:nth-of-type(3) { left: 613px; }
  .category:nth-of-type(4) { left: 886px; }
  .category svg {
    position: absolute;
    left: 0;
    top: 0;
    width: 250px;
    height: 710px;
  }
  .category-heading {
    position: absolute;
    left: 25px;
    width: 190px;
    top: 0;
    height: 105px;
    display: flex;
    align-items: center;
    justify-content: center;
    text-align: center;
    font-family: "Jost", "Futura", sans-serif;
    font-weight: 600;
    font-size: 19px;
    line-height: 1.1;
    letter-spacing: 0.8px;
    padding-top: 22px;
  }
  .preservation .category-heading { color: var(--green-head); }
  .capital .category-heading { color: var(--blue-head); }
  .realestate .category-heading { color: var(--brown-head); }
  .alternatives .category-heading { color: var(--gray-head); }
  .category-items {
    position: absolute;
    left: 47px;
    top: 198px;
    width: 175px;
    list-style: none;
    font-size: 17px;
    line-height: 25px;
    color: var(--text-body);
  }
  .category-items li {
    position: relative;
    padding-left: 11px;
  }
  .category-items li::before {
    content: "•";
    position: absolute;
    left: 0;
    font-size: 12px;
  }
  .category-items.plain li { padding-left: 0; }
  .category-items.plain li::before { content: none; }
  .capital .category-items { left: 52px; }
</style>
</head>
<body>
<main class="slide">
  <h1 class="slide-title">Total Asset Allocation</h1>
  <div class="brand">
    <span class="brand-dot"></span>
    <span class="brand-name">Korvane LLC</span>
  </div>

  <svg width="0" height="0" style="position:absolute">
    <defs>
      <linearGradient id="card-fill" x1="0" y1="0" x2="0" y2="1">
        <stop offset="0" stop-color="#fbfbfb"/>
        <stop offset="0.55" stop-color="#ececec"/>
        <stop offset="1" stop-color="#a4a4a8"/>
      </linearGradient>
      <linearGradient id="card-side" x1="0" y1="0" x2="1" y2="0">
        <stop offset="0" stop-color="#000" stop-opacity="0.12"/>
        <stop offset="0.4" stop-color="#000" stop-opacity="0"/>
      </linearGradient>
      <linearGradient id="reflection-fill" x1="0" y1="0" x2="0" y2="1">
        <stop offset="0" stop-color="#ffffff" stop-opacity="0.45"/>
        <stop offset="1" stop-color="#ffffff" stop-opacity="0"/>
      </linearGradient>
      <radialGradient id="floor-shadow">
        <stop offset="0" stop-color="#3b4450" stop-opacity="0.55"/>
        <stop offset="1" stop-color="#3b4450" stop-opacity="0"/>
      </radialGradient>
    </defs>
  </svg>

  <section class="category preservation">
    <svg viewBox="0 0 250 710" aria-hidden="true">
      <ellipse cx="122" cy="484" rx="115" ry="9" fill="url(#floor-shadow)"/>
      <rect x="25" y="500" width="190" height="210" rx="38" fill="url(#reflection-fill)"/>
      <path d="M25 86 C8 86 0 96 0 118 H25 Z" fill="var(--green-dark)"/>
      <rect x="25" y="0" width="190" height="475" rx="38" fill="url(#card-fill)"/>
      <rect x="25" y="0" width="190" height="475" rx="38" fill="url(#card-side)"/>
      <path d="M27 445 V40 A38 38 0 0 1 65 2 H178" fill="none" stroke="var(--green)" stroke-width="4"/>
      <path d="M0 118 H218 C240 118 250 124 250 140 V171 H20 C8 171 0 165 0 155 Z" fill="var(--green)"/>
      <path d="M215 171 H250 V190 C250 200 235 206 215 208 Z" fill="var(--green-dark)"/>
    </svg>
    <h2 class="category-heading">PRESERVATION</h2>
    <ul class="category-items">
      <li>Cash</li>
      <li>Checking/ Savings Accounts</li>
      <li>Money Market Funds</li>
      <li>CD’s</li>
      <li>Fixed Annuities</li>
    </ul>
  </section>

  <section class="category capital">
    <svg viewBox="0 0 250 710" aria-hidden="true">
      <ellipse cx="122" cy="484" rx="115" ry="9" fill="url(#floor-shadow)"/>
      <rect x="25" y="500" width="190" height="210" rx="38" fill="url(#reflection-fill)"/>
      <path d="M25 86 C8 86 0 96 0 118 H25 Z" fill="var(--blue-dark)"/>
      <rect x="25" y="0" width="190" height="475" rx="38" fill="url(#card-fill)"/>
      <rect x="25" y="0" width="190" height="475" rx="38" fill="url(#card-side)"/>
      <path d="M27 445 V40 A38 38 0 0 1 65 2 H178" fill="none" stroke="var(--blue)" stroke-width="4"/>
      <path d="M0 118 H218 C240 118 250 124 250 140 V171 H20 C8 171 0 165 0 155 Z" fill="var(--blue)"/>
      <path d="M215 171 H250 V190 C250 200 235 206 215 208 Z" fill="var(--blue-dark)"/>
    </svg>
    <h2 class="category-heading">CAPITAL<br>MARKETS</h2>
    <ul class="category-items plain">
      <li>Publicly-traded stocks and bonds</li>
    </ul>
  </section>

  <section class="category realestate">
    <svg viewBox="0 0 250 710" aria-hidden="true">
      <ellipse cx="122" cy="484" rx="115" ry="9" fill="url(#floor-shadow)"/>
      <rect x="25" y="500" width="190" height="210" rx="38" fill="url(#reflection-fill)"/>
      <path d="M25 86 C8 86 0 96 0 118 H25 Z" fill="var(--brown-dark)"/>
      <rect x="25" y="0" width="190" height="475" rx="38" fill="url(#card-fill)"/>
      <rect x="25" y="0" width="190" height="475" rx="38" fill="url(#card-side)"/>
      <path d="M27 445 V40 A38 38 0 0 1 65 2 H178" fill="none" stroke="var(--brown)" stroke-width="4"/>
      <path d="M0 118 H218 C240 118 250 124 250 140 V171 H20 C8 171 0 165 0 155 Z" fill="var(--brown)"/>
      <path d="M215 171 H250 V190 C250 200 235 206 215 208 Z" fill="var(--brown-dark)"/>
    </svg>
    <h2 class="category-heading">REAL ESTATE</h2>
    <ul class="category-items">
      <li>Single-Family Residences</li>
      <li>Retail</li>
      <li>Industrial</li>
      <li>Multifamily</li>
      <li>Office</li>
    </ul>
  </section>

  <section class="category alternatives">
    <svg viewBox="0 0 250 710" aria-hidden="true">
      <ellipse cx="122" cy="484" rx="115" ry="9" fill="url(#floor-shadow)"/>
      <rect x="25" y="500" width="190" height="210" rx="38" fill="url(#reflection-fill)"/>
      <path d="M25 86 C8 86 0 96 0 118 H25 Z" fill="var(--gray-dark)"/>
      <rect x="25" y="0" width="190" height="475" rx="38" fill="url(#card-fill)"/>
      <rect x="25" y="0" width="190" height="475" rx="38" fill="url(#card-side)"/>
      <path d="M27 445 V40 A38 38 0 0 1 65 2 H178" fill="none" stroke="var(--gray)" stroke-width="4"/>
      <path d="M0 118 H218 C240 118 250 124 250 140 V171 H20 C8 171 0 165 0 155 Z" fill="var(--gray)"/>
      <path d="M215 171 H250 V190 C250 200 235 206 215 208 Z" fill="var(--gray-dark)"/>
    </svg>
    <h2 class="category-heading">ALTERNATIVES</h2>
    <ul class="category-items">
      <li>Private Equity</li>
      <li>Private Credit</li>
      <li>Cryptocurrency</li>
      <li>Asset-backed Loans</li>
      <li>Tax Liens</li>
      <li>Oil &amp; Gas</li>
      <li>Litigation Finance</li>
      <li>Royalties</li>
    </ul>
  </section>
</main>
</body>
</html>
```